Web design project for exciting Australian start-up

Background
We are looking for a creative and talented web design artist to work alongside our market leading web developer.
• You will be required to create a modern and clean design theme for our website, incorporating selected rustic colour scheme elements for our exciting Australian start-up to operate within the coffee industry.
reoccurring work to be expected to flow to the successful designer.
Requirements
• c. 5 - 10 page website
• Landing page
• Log in/ out
• 404 template
• Typography is emphasised
• Please use either a) typemarrow.com, b) free web fonts, c) brindle fonts
• All design elements in vector format
• Preferably with icons for each header title(i.e. about us, how it works etc) but designer have free reign over how the site looks, so might not be applicable
• All pages to be responsive
• Down to eSlab resolution

High level visual design brief attached - additional pages to be worked from base design.

Design inspiration
• We would like to use design elements from the following sources:
http://www.zandrix.com/halcyon/ (Functionality)
Colour scheme refer to logo and complementary style guide

```html
<!DOCTYPE html>
<html lang="en">
<head>
<meta charset="utf-8">
<title>Bean Circuit – Market Place</title>
<link rel="stylesheet" href="https://fonts.googleapis.com/css2?family=Arimo:wght@400;700&display=swap">
<style>
:root{
  --orange:#e09c50;
  --olive:#6b6b48;
  --ink:#222;
  --panel:#ebebeb;
  --page:#e5e5e5;
  --header:#f2f2f2;
  --footer:#4b4c48;
  --field:#f5f5f5;
  --field-active:#c9c8c6;
  --menu:#cdcccb;
}
*{margin:0;padding:0;box-sizing:border-box}
html,body{width:1200px;height:752px;overflow:hidden}
body{position:relative;font-family:Arimo,Arial,sans-serif;background:var(--page);color:var(--ink)}
.abs{position:absolute}

.top-band{left:0;top:0;width:1200px;height:8px;background:var(--orange)}
.site-header{left:0;top:8px;width:1200px;height:104px;background:var(--header)}
.header-rule{left:0;top:112px;width:1200px;height:4px;background:#4a4a4a}

.brand{left:200px;top:38px;display:flex;align-items:center;gap:12px;font-weight:700;font-size:28px;letter-spacing:1px;color:#1e1e1e}
.brand-dot{width:60px;height:60px;border-radius:50%;background:var(--orange)}

.account-btn{top:40px;height:35px;border:1px solid #c9c9c9;background:#efefef;font-size:12px;font-weight:700;display:flex;align-items:center;justify-content:center}
.my-account{left:725px;width:113px;color:var(--orange)}
.session{left:847px;width:152px;justify-content:space-around}
.session .on{color:var(--orange)}
.session .sep{width:0;height:24px;border-left:1px dotted #999}
.session .out{color:#333}

.market-title{left:200px;top:264px;font-size:40px;color:var(--orange);font-weight:400}
.cta{height:51px;display:flex;font-size:20px;color:#fff}
.cta .label{display:flex;align-items:center;padding-left:20px}
.cta .arrow{width:49px;display:flex;align-items:center;justify-content:center}
.start-tender{left:200px;top:335px;width:221px}
.start-tender .label{background:var(--olive);width:173px}
.start-tender .arrow{background:var(--orange)}
.launch-search{left:714px;top:431px;width:221px}
.launch-search .label{background:var(--orange);width:172px;padding-left:13px}
.launch-search .arrow{background:var(--olive)}

.search-panel{left:481px;top:137px;width:507px;height:416px;background:var(--panel);border:1px solid #dcdcdc;box-shadow:0 0 3px rgba(0,0,0,.12)}
.panel-title{left:501px;top:153px;font-size:19px;font-weight:700;color:var(--orange)}
.field{left:504px;width:165px;height:29px;background:var(--field);border:1px solid #c5c5c5;box-shadow:1px 1px 2px rgba(0,0,0,.15);font-size:12px;display:flex;align-items:center;padding-left:12px}
.field.active{background:var(--field-active)}

.menu{width:138px;background:var(--menu);box-shadow:1px 1px 2px rgba(0,0,0,.2);font-size:10px}
.menu div,.submenu div{display:flex;align-items:center;padding-left:10px}
.menu .sel{background:var(--orange)}
.submenu{left:813px;width:137px;background:var(--menu);font-size:10px}

.side-share{left:1174px;top:294px;width:26px}
.side-share div{height:28px;display:flex;align-items:center;justify-content:center}

.site-footer{left:0;top:578px;width:1200px;height:174px;background:var(--footer);color:#fff}
.foot-head{top:598px;font-size:12px;font-weight:700;color:var(--orange)}
.foot-links{top:619px;font-size:10px;line-height:16.5px;color:#fff;list-style:none}
.tweet{left:594px;top:616px;width:180px;font-size:10px;line-height:11.5px;color:#fff}
.tweet .handle{color:#e22}
.follow{left:894px;top:617px;display:flex;gap:4px}
.follow span{width:18px;height:18px;display:block}
.counter{left:1102px;top:620px;font-size:12px;font-weight:700;color:var(--orange)}
.dots{top:706px;height:0;border-top:1px dotted #9a9a94}
.copyright{left:0;top:725px;width:1180px;text-align:center;font-size:12px;color:#fff}
</style>
</head>
<body>
<div class="abs top-band"></div>
<header class="abs site-header"></header>
<div class="abs header-rule"></div>

<div class="abs brand"><span>BEAN</span><span class="brand-dot"></span><span>CIRCUIT</span></div>

<div class="abs account-btn my-account">My Account</div>
<div class="abs account-btn session"><span class="on">Logged In</span><span class="sep"></span><span class="out">Log Out</span></div>

<h1 class="abs market-title">Market Place</h1>
<div class="abs cta start-tender"><span class="label">Start A Tender</span><span class="arrow"><svg width="20" height="28" viewBox="0 0 20 28"><path d="M2 2 L18 14 L2 26 Z" fill="#fff" stroke="#fff" stroke-width="3" stroke-linejoin="round"/></svg></span></div>

<section class="abs search-panel"></section>
<h2 class="abs panel-title">Selcet</h2>

<div class="abs field active" style="top:190px">Tender type</div>
<div class="abs field" style="top:238px">Quantity ( kg )</div>
<div class="abs field" style="top:287px">Wholesaler</div>
<div class="abs field" style="top:382px">Machinery</div>
<div class="abs field" style="top:423px">Barista Trianing</div>
<div class="abs field" style="top:464px">Accessories</div>
<div class="abs field" style="top:503px">Promotion Support</div>

<div class="abs menu" style="left:675px;top:190px">
  <div style="height:29px">One-Off</div>
  <div class="sel" style="height:26px">Recurring</div>
</div>
<div class="abs submenu" style="top:220px">
  <div style="height:26px;padding-top:6px">6 Months</div>
  <div style="height:29px">12 Months</div>
</div>

<div class="abs menu" style="left:675px;top:287px">
  <div style="height:23px">Castellan</div>
  <div class="sel" style="height:19px">Di Marra</div>
  <div style="height:21px">Roastex</div>
  <div style="height:22px">Valtoria</div>
</div>
<div class="abs submenu" style="top:310px">
  <div style="height:28px;padding-top:4px">Blend A</div>
  <div style="height:27px">Blend B</div>
</div>

<div class="abs cta launch-search"><span class="label">Launch Search</span><span class="arrow"><svg width="20" height="28" viewBox="0 0 20 28"><path d="M2 2 L18 14 L2 26 Z" fill="#fff" stroke="#fff" stroke-width="3" stroke-linejoin="round"/></svg></span></div>

<nav class="abs side-share" aria-label="Share">
  <div style="background:#c2581a"><svg width="10" height="8" viewBox="0 0 10 8"><rect x=".5" y=".5" width="9" height="7" fill="none" stroke="#fff"/><path d="M.5 .5 L5 4.5 L9.5 .5" fill="none" stroke="#fff"/></svg></div>
  <div style="background:#2a8fc0"></div>
  <div style="background:#3b5a99"></div>
  <div style="background:#3e67c4"></div>
  <div style="background:#b3222a"></div>
  <div style="background:#6b4f40"></div>
  <div style="background:#3a3a3a"><svg width="9" height="9" viewBox="0 0 9 9"><circle cx="3.5" cy="3.5" r="2.5" fill="none" stroke="#fff" stroke-width="1.3"/><path d="M5.5 5.5 L8.3 8.3" stroke="#fff" stroke-width="1.5"/></svg></div>
</nav>

<footer class="abs site-footer"></footer>
<h3 class="abs foot-head" style="left:200px">Helpfull Info</h3>
<ul class="abs foot-links" style="left:200px"><li>About Us</li><li>Media Enquiries</li><li>Terms &amp; Conditions</li><li>Privocy Policy</li></ul>
<h3 class="abs foot-head" style="left:417px">Who We Are</h3>
<ul class="abs foot-links" style="left:417px"><li>How it works</li><li>FAQ</li><li>Contact Us</li></ul>
<h3 class="abs foot-head" style="left:594px;top:596px">Tweets</h3>
<p class="abs tweet"><span class="handle">RT @lena</span> Talking about @quillmarket's values and mission at #PressSummit. See the list here: http://lnk.to/qW3rT8aZ yesterday</p>
<h3 class="abs foot-head" style="left:894px;top:596px">Follow Us</h3>
<div class="abs follow">
  <span style="background:#3b5a99"></span><span style="background:#3fa9d9"></span><span style="background:#c8483a"></span><span style="background:#c7303a"></span><span style="background:#f2f2f2"></span>
</div>
<div class="abs counter">x18</div>

<div class="abs dots" style="left:200px;width:368px"></div>
<svg class="abs" style="left:584px;top:689px" width="28" height="26" viewBox="0 0 28 26" aria-hidden="true">
  <path d="M4 12 H20 V16 C20 20 17 22 12 22 C7 22 4 20 4 16 Z" fill="none" stroke="#e09c50" stroke-width="1.6"/>
  <path d="M20 13 C25 13 25 18 20 18" fill="none" stroke="#e09c50" stroke-width="1.5"/>
  <path d="M2 24 H22" stroke="#e09c50" stroke-width="1.6"/>
  <path d="M9 9 C7 6 11 5 9 2 M13 9 C11 6 15 5 13 2" fill="none" stroke="#e09c50" stroke-width="1.3"/>
</svg>
<div class="abs dots" style="left:629px;width:369px"></div>
<p class="abs copyright">Copy right@ Bean Circuit</p>
</body>
</html>
```